BUSINESS CARD DESIGN

NAME- DALE VORSKIN
PHONE NUMER - 555- 714-9082
EMAIL- OFFICE@TRV-GROUNDMAKRZ.COM
BACK OF CARD- SPEACIALIZES IN LAND CLEARING, FORESTRY MUCLHING AND EXCAVATION

Contact Information for Business Card

NAME- DALE VORSKIN PHONE NUMER - 555- 714-9082 EMAIL- OFFICE@TRV-GROUNDMAKRZ.COM BACK OF CARD- SPEACIALIZES IN LAND CLEARING , MUCLHING AND EXCAVATION

```html
<!DOCTYPE html>
<html lang="en">
<head>
<meta charset="utf-8">
<title>Trevan Groundmakrz LLC – Business Card</title>
<link rel="stylesheet" href="https://fonts.googleapis.com/css2?family=Jost:wght@400;500;700&display=swap">
<style>
  :root {
    --page-bg: #5a5a5a;
    --card-white: #f7f7f7;
    --card-white-edge: #e4e4e4;
    --card-black: #070707;
    --gold: #f2ae1c;
    --ink: #111111;
    --muted: #4a4a4a;
    --light-text: #f4f4f4;
  }
  * { box-sizing: border-box; margin: 0; padding: 0; }
  html, body { width: 1200px; height: 900px; overflow: hidden; }
  body {
    background: var(--page-bg);
    font-family: "Jost", "Futura", sans-serif;
    position: relative;
  }
  .card {
    position: absolute;
    left: 290px;
    width: 620px;
    height: 354px;
    border-radius: 34px;
    overflow: hidden;
    box-shadow: 0 14px 30px rgba(0,0,0,0.35);
  }
  /* Back side */
  .card-back {
    top: 64px;
    background: linear-gradient(160deg, #ffffff 0%, var(--card-white) 55%, var(--card-white-edge) 100%);
    display: flex;
    flex-direction: column;
    align-items: center;
  }
  .back-brand {
    margin-top: 84px;
    display: flex;
    align-items: center;
    gap: 12px;
    color: var(--ink);
    font-weight: 700;
    font-size: 30px;
    letter-spacing: 1px;
  }
  .brand-dot {
    width: 20px; height: 20px;
    border-radius: 50%;
    background: currentColor;
  }
  .back-rule {
    margin-top: 46px;
    width: 420px;
    height: 1.5px;
    background: linear-gradient(90deg, transparent 0%, var(--gold) 20%, var(--gold) 80%, transparent 100%);
  }
  .back-heading {
    margin-top: 18px;
    font-weight: 500;
    font-size: 24px;
    color: var(--ink);
  }
  .back-services {
    margin-top: 4px;
    font-size: 22px;
    color: var(--muted);
  }
  /* Front side */
  .card-front {
    top: 482px;
    background: var(--card-black);
  }
  .front-brand {
    position: absolute;
    left: 40px;
    top: 118px;
    width: 250px;
    color: var(--gold);
    text-align: center;
  }
  .front-brand-name {
    display: flex;
    align-items: center;
    justify-content: center;
    gap: 10px;
    font-weight: 700;
    font-size: 24px;
    line-height: 1.15;
    letter-spacing: 0.5px;
  }
  .front-brand-name .brand-dot { width: 16px; height: 16px; flex: none; }
  .front-brand-sub {
    margin-top: 6px;
    font-weight: 700;
    font-size: 13px;
    letter-spacing: 5px;
  }
  .front-brand-phone {
    margin-top: 6px;
    padding-top: 6px;
    border-top: 1px solid var(--gold);
    font-weight: 700;
    font-size: 13px;
    letter-spacing: 6px;
  }
  .front-divider {
    position: absolute;
    left: 352px;
    top: 150px;
    width: 1.5px;
    height: 112px;
    background: var(--gold);
  }
  .contact {
    position: absolute;
    left: 378px;
    top: 150px;
    color: var(--light-text);
  }
  .contact-name {
    color: var(--gold);
    font-weight: 700;
    font-size: 26px;
    letter-spacing: 0.5px;
    margin-bottom: 10px;
  }
  .contact-line {
    display: flex;
    align-items: center;
    gap: 10px;
    font-size: 19px;
    line-height: 1.5;
  }
  .contact-line svg { width: 18px; height: 18px; flex: none; }
</style>
</head>
<body>

  <section class="card card-back" aria-label="Card back">
    <div class="back-brand"><span class="brand-dot"></span>TREVAN GROUNDMAKRZ</div>
    <div class="back-rule"></div>
    <p class="back-heading">Speacializes In</p>
    <p class="back-services">Land Clearing, Muclhing And Excavation</p>
  </section>

  <section class="card card-front" aria-label="Card front">
    <div class="front-brand">
      <div class="front-brand-name"><span class="brand-dot"></span>TREVAN GROUNDMAKRZ</div>
      <div class="front-brand-sub">LLC</div>
      <div class="front-brand-phone">555-714-9082</div>
    </div>

    <div class="front-divider"></div>

    <div class="contact">
      <p class="contact-name">DALE VORSKIN</p>
      <p class="contact-line">
        <svg viewBox="0 0 24 24" aria-hidden="true"><path fill="var(--gold)" d="M6.6 10.8a15.1 15.1 0 0 0 6.6 6.6l2.2-2.2a1 1 0 0 1 1-.25 11.4 11.4 0 0 0 3.6.57 1 1 0 0 1 1 1V20a1 1 0 0 1-1 1A17 17 0 0 1 3 4a1 1 0 0 1 1-1h3.5a1 1 0 0 1 1 1c0 1.25.2 2.45.57 3.57a1 1 0 0 1-.25 1z"/></svg>
        555- 714-9082
      </p>
      <p class="contact-line">
        <svg viewBox="0 0 24 24" aria-hidden="true"><rect x="2" y="5" width="20" height="14" rx="1.5" fill="var(--gold)"/><path d="M3 6l9 7 9-7" fill="none" stroke="var(--card-black)" stroke-width="1.8"/></svg>
        office@trv-groundmakrz.com
      </p>
    </div>
  </section>

</body>
</html>
```